Corvel Capital LLC

Need Professional Business cards for New Investment Fund

Target Market(s)

High Quality investors

Industry/Entity Type

Financial

Contact Information for Business Card

Phone Number +1 555 284 6190
Name Lukas Varenko
Title Fund Manager
email lv@FundQuillory.com
Website www.FundQuillory.com

Colors

Designer to choose colors to be used in the design.

Requirements
Must have
• Must have our Logo and all of the above. Must be made so lettering and loge can be raised

```html
<!DOCTYPE html>
<html lang="en">
<head>
<meta charset="utf-8">
<title>Quillory Capital LLC – Business Card</title>
<link rel="stylesheet" href="https://fonts.googleapis.com/css2?family=Roboto:wght@400;500;700&display=swap">
<style>
  :root {
    --backdrop: #bdbdbd;
    --slate: #3a423d;
    --lime: #8dc21f;
    --paper: #f4f4f2;
    --ink-light: #f0f0ee;
    --ink-soft: #e2e4e1;
  }
  * { margin: 0; padding: 0; box-sizing: border-box; }
  html, body { width: 1200px; height: 1138px; overflow: hidden; }
  body {
    background: var(--backdrop);
    font-family: "Roboto", Arial, sans-serif;
    position: relative;
  }
  .card {
    position: absolute;
    width: 620px;
    height: 374px;
    border-radius: 14px;
    overflow: hidden;
  }
  .card-front {
    left: 274px; top: 186px;
    background: var(--slate);
    display: flex; align-items: center; justify-content: center;
  }
  .brand-name {
    font-family: "Roboto", Arial, sans-serif;
    font-weight: 500;
    letter-spacing: 2px;
    line-height: 1;
  }
  .card-front .brand-name { color: var(--ink-light); font-size: 48px; margin-top: 10px; }
  .card-back { left: 276px; top: 608px; background: var(--paper); }
  .card-back .brand-name {
    position: absolute; left: 36px; top: 112px;
    color: var(--slate); font-size: 36px;
  }
  .divider { position: absolute; left: 0; top: 0; width: 620px; height: 374px; }
  .holder {
    position: absolute; right: 30px; top: 208px; text-align: right; color: var(--ink-light);
  }
  .holder-name { font-size: 22px; font-weight: 700; }
  .holder-title { font-size: 15px; color: var(--ink-soft); margin-top: 7px; }
  .contact-list {
    position: absolute; right: 30px; top: 276px; list-style: none;
    color: var(--ink-soft); font-size: 15px; text-align: right;
  }
  .contact-list li { height: 23.5px; display: flex; align-items: center; justify-content: flex-end; gap: 7px; }
  .contact-list svg { width: 14px; height: 14px; fill: var(--ink-soft); }
  .address {
    position: absolute; left: 36px; top: 300px; color: var(--ink-soft);
    font-size: 15px; line-height: 23.5px; font-style: normal;
  }
</style>
</head>
<body>
  <section class="card card-front">
    <span class="brand-name">QUILLORY</span>
  </section>

  <section class="card card-back">
    <svg class="divider" viewBox="0 0 620 374" aria-hidden="true">
      <path fill="#3a423d" d="M0,250 C180,262 400,200 620,168 L620,374 L0,374 Z"/>
      <path fill="none" stroke="#8dc21f" stroke-width="5" d="M0,238 C180,250 400,188 620,156"/>
    </svg>
    <span class="brand-name">QUILLORY</span>
    <div class="holder">
      <div class="holder-name">Lukas Varenko</div>
      <div class="holder-title">Fund Manager</div>
    </div>
    <ul class="contact-list">
      <li>+1 555 284 6190
        <svg viewBox="0 0 16 16"><path d="M1 5c0-2 3-3 7-3s7 1 7 3v1h-4V5H5v1H1z"/><path d="M4 7h8l2 6H2z"/></svg>
      </li>
      <li>lv@FundQuillory.com
        <svg viewBox="0 0 16 16"><path d="M1 3h14v10H1z M2.5 4.5 8 9l5.5-4.5" fill="none" stroke="#e2e4e1" stroke-width="1.5"/></svg>
      </li>
      <li>www.FundQuillory.com
        <svg viewBox="0 0 16 16"><circle cx="8" cy="8" r="6.5" fill="none" stroke="#e2e4e1" stroke-width="1.3"/><path d="M1.5 8h13M8 1.5v13" stroke="#e2e4e1" stroke-width="1"/><ellipse cx="8" cy="8" rx="3" ry="6.5" fill="none" stroke="#e2e4e1" stroke-width="1"/></svg>
      </li>
    </ul>
    <address class="address">48 Alder Row<br>Millbrook, NJ, 08960</address>
  </section>
</body>
</html>
```